BOLD & MINIMALIST DESIGN NEEDED

We want a very bold but minimalistic business card design that is impactful and utilizes both sides of the business card. Our current logo is included for your use.

We want bold fonts and good use of negative space. We don't want the logo to overpower the design.

Target Market(s)

Professionals who are building new commercial buildings.

Industry/Entity Type

Construction

Contact Information for Business Card

Name, Title, email, office phone, cell phone, website

Font styles to use
Serif
Sans Serif

Requirements
Must have
• Bold design!

```html
<!DOCTYPE html>
<html lang="en">
<head>
<meta charset="utf-8">
<title>Ridgeline Design + Build — Business Card</title>
<link href="https://fonts.googleapis.com/css2?family=Montserrat:wght@400;500;700&display=swap" rel="stylesheet">
<style>
  :root {
    --backdrop: #1d1d1d;
    --card-white: #f4f4f4;
    --brand-green: #7cbd3e;
    --ink: #222222;
    --ink-soft: #333333;
  }
  * { margin: 0; padding: 0; box-sizing: border-box; }
  html, body {
    width: 1200px; height: 1059px; overflow: hidden;
    background: var(--backdrop);
    font-family: "Montserrat", sans-serif;
  }
  .canvas { position: relative; width: 1200px; height: 1059px; }

  .card {
    position: absolute;
    border-radius: 18px;
    overflow: hidden;
  }
  .card--front { left: 257px; top: 89px; width: 687px; height: 390px; background: var(--card-white); }
  .card--back  { left: 254px; top: 547px; width: 693px; height: 393px; background: var(--brand-green); }

  .brand {
    position: absolute;
    text-align: center;
    font-weight: 700;
    line-height: 1;
  }
  .brand__name { display: block; letter-spacing: 0.01em; }
  .brand__tag  { display: block; letter-spacing: 0.32em; margin-top: 8px; }

  .card--front .brand { left: 40px; width: 282px; top: 168px; color: var(--ink); }
  .card--front .brand__name { font-size: 40px; }
  .card--front .brand__tag  { font-size: 14px; }

  .card--back .brand { left: 0; width: 693px; top: 178px; color: #ffffff; }
  .card--back .brand__name { font-size: 62px; }
  .card--back .brand__tag  { font-size: 21px; margin-top: 10px; }

  .divider {
    position: absolute; left: 343px; top: 109px;
    width: 1px; height: 175px; background: var(--brand-green);
  }

  .person { position: absolute; left: 374px; top: 106px; }
  .person__name {
    font-size: 30px; font-weight: 700; color: var(--brand-green);
    letter-spacing: 0.01em; line-height: 1;
  }
  .person__title {
    font-size: 18px; font-weight: 500; color: var(--ink-soft);
    margin-top: 2px;
  }

  .contacts { position: absolute; left: 374px; top: 180px; list-style: none; }
  .contacts__item {
    display: flex; align-items: center; gap: 6px;
    height: 28px;
    font-size: 18px; font-weight: 500; color: var(--ink-soft);
  }
  .contacts__icon { width: 12px; height: 12px; fill: var(--brand-green); flex: none; }
  .contacts__accent { color: var(--brand-green); }

  .edge-band { position: absolute; left: 0; bottom: 0; width: 687px; height: 15px; }
</style>
</head>
<body>
<main class="canvas">

  <section class="card card--front" aria-label="Card front">
    <div class="brand">
      <span class="brand__name">RIDGELINE</span>
      <span class="brand__tag">DESIGN + BUILD</span>
    </div>

    <div class="divider"></div>

    <div class="person">
      <p class="person__name">DANA WHITFIELD</p>
      <p class="person__title">Owner/CEO</p>
    </div>

    <ul class="contacts">
      <li class="contacts__item">
        <svg class="contacts__icon" viewBox="0 0 12 12" aria-hidden="true"><path d="M2.3 0.8l2 2-1 1.3c.7 1.6 2 2.9 3.6 3.6l1.3-1 2 2-1.3 2.3C4.6 10.6 1.4 7.4.8 3.1z"/></svg>
        <span>07 5550 1234</span>
      </li>
      <li class="contacts__item">
        <svg class="contacts__icon" viewBox="0 0 12 12" aria-hidden="true"><path d="M3 0h6v12H3zM4 1.5v8h4v-8zM5.5 10.2h1v1h-1z" fill-rule="evenodd"/></svg>
        <span>0400 555 019</span>
      </li>
      <li class="contacts__item">
        <svg class="contacts__icon" viewBox="0 0 12 12" aria-hidden="true"><path d="M0 2h12v8H0zM1 3l5 4 5-4v-.1H1z"/></svg>
        <span>info@ridgelinebuild.com</span>
      </li>
      <li class="contacts__item">
        <svg class="contacts__icon" viewBox="0 0 12 12" aria-hidden="true"><circle cx="6" cy="6" r="6"/></svg>
        <span>www.<span class="contacts__accent">ridgelinebuild</span>.com</span>
      </li>
    </ul>

    <svg class="edge-band" viewBox="0 0 687 15" preserveAspectRatio="none" aria-hidden="true">
      <polygon points="0,0 352,0 332,15 0,15" fill="var(--brand-green)"/>
      <polygon points="362,0 687,0 687,15 342,15" fill="var(--ink)"/>
    </svg>
  </section>

  <section class="card card--back" aria-label="Card back">
    <div class="brand">
      <span class="brand__name">RIDGELINE</span>
      <span class="brand__tag">DESIGN + BUILD</span>
    </div>
  </section>

</main>
</body>
</html>
```